New Property development signage

large poster for a new development.
3 metres x 2 metres. To include the following.

Tresswick Gardens
TO LET
LUXURY FULLY FURNISHED LARGE
2 AND 3 BED APARTMENTS
Garrold Estates
362 4150
www.garroldestates-example.com

Need this to be large simple writing with Garrold estates logo on the bottom

Target Market(s)

High end rental property market

Industry/Entity Type

Real Estate Development

Colors
000000
cbcbcb
0555a3

Requirements
Must have
• Name of the development must be in a different font, classic style
Nice to have
• Light Grey background, blues for colours
Should not have
• anymore than 3 /4 colours

```html
<!DOCTYPE html>
<html lang="en">
<head>
<meta charset="utf-8">
<title>Tresswick Gardens – To Let</title>
<link rel="stylesheet" href="https://fonts.googleapis.com/css2?family=Pinyon+Script&family=Merriweather:wght@700;900&display=swap">
<style>
  :root {
    --brand-blue: #0555a3;
    --navy: #283889;
    --paper: #ffffff;
    --page: #cbcbcb;
    --photo-warm: #c9a888;
    --photo-light: #e6e2dc;
    --photo-blue: #8fa6c4;
  }
  html, body {
    margin: 0;
    padding: 0;
    overflow: hidden;
    background: var(--page);
  }
  .poster {
    position: relative;
    width: 800px;
    height: 1200px;
    margin: 0 auto;
    background: var(--paper);
    overflow: hidden;
    font-family: "Merriweather", Georgia, serif;
    text-align: center;
  }
  .development-name {
    position: absolute;
    top: 108px;
    left: 0;
    width: 100%;
    margin: 0;
    font-family: "Pinyon Script", cursive;
    font-weight: 400;
    font-size: 86px;
    line-height: 1;
    color: var(--brand-blue);
  }
  .status {
    position: absolute;
    top: 240px;
    left: 0;
    width: 100%;
    margin: 0;
    font-size: 36px;
    font-weight: 900;
    color: var(--brand-blue);
    letter-spacing: 0.5px;
  }
  .gallery {
    position: absolute;
    top: 318px;
    left: 135px;
    width: 537px;
    height: 239px;
    display: grid;
    grid-template-columns: repeat(3, 1fr);
    grid-template-rows: repeat(2, 1fr);
    gap: 1px;
    background: var(--paper);
  }
  .gallery .room { display: block; }
  .room.kitchen  { background: linear-gradient(180deg, var(--photo-light), var(--photo-warm)); }
  .room.lounge   { background: linear-gradient(180deg, #a9c9c4, var(--photo-warm)); }
  .room.living   { background: linear-gradient(180deg, var(--photo-light), #b07a5a); }
  .room.bedroom  { background: linear-gradient(180deg, var(--photo-light), var(--photo-blue)); }
  .room.sitting  { background: linear-gradient(180deg, var(--photo-light), #b48a6a); }
  .room.bedroom-two { background: linear-gradient(180deg, var(--photo-light), #7f8fb5); }
  .headline {
    position: absolute;
    left: 0;
    width: 100%;
    margin: 0;
    font-size: 37px;
    font-weight: 900;
    color: var(--brand-blue);
    letter-spacing: -1px;
    line-height: 1;
  }
  .headline.line-one { top: 617px; }
  .headline.line-two { top: 707px; }
  .phone {
    position: absolute;
    top: 798px;
    left: 0;
    width: 100%;
    margin: 0;
    font-size: 54px;
    font-weight: 900;
    color: var(--navy);
    line-height: 1;
    letter-spacing: 1px;
  }
  .agent {
    position: absolute;
    top: 878px;
    left: 200px;
    width: 400px;
  }
  .agent-name {
    margin: 0;
    font-size: 46px;
    font-weight: 900;
    color: var(--navy);
    line-height: 1.1;
  }
  .agent-services {
    margin: 14px 0 0;
    font-size: 15px;
    font-weight: 700;
    color: var(--navy);
  }
  .website {
    position: absolute;
    top: 1034px;
    left: 0;
    width: 100%;
    margin: 0;
    font-size: 28px;
    font-weight: 900;
    color: var(--navy);
  }
</style>
</head>
<body>
  <main class="poster">
    <h1 class="development-name">Tresswick Gardens</h1>
    <p class="status">TO LET</p>

    <section class="gallery">
      <span class="room kitchen" role="img" aria-label="Photo of a fitted kitchen with appliances"></span>
      <span class="room lounge" role="img" aria-label="Photo of a lounge with fireplace and bay window"></span>
      <span class="room living" role="img" aria-label="Photo of a living room with wooden floor and sofas"></span>
      <span class="room bedroom" role="img" aria-label="Photo of a bedroom with double bed and wardrobes"></span>
      <span class="room sitting" role="img" aria-label="Photo of a sitting room with sofas and fireplace"></span>
      <span class="room bedroom-two" role="img" aria-label="Photo of a second bedroom with double bed"></span>
    </section>

    <p class="headline line-one">LUXURY FULLY FURNISHED LARGE</p>
    <p class="headline line-two">2 AND 3 BED APARTMENTS</p>

    <p class="phone">362 4150</p>

    <div class="agent">
      <p class="agent-name">Garrold Estates</p>
      <p class="agent-services">Sales • Lettings • Management • B.E.R. Certs</p>
    </div>

    <p class="website">www.garroldestates-example.com</p>
  </main>
</body>
</html>
```